Im open to ideas.. I was thinking on my business cards aswell as my logo. a place for my name. email. phone number and abn..

ive attched a file with my business logo. which i dont love the colours.. i was think a dark background with charcoal letters so something along those colour schumes but im open to ideas..

BRM Constructions

```html
<!DOCTYPE html>
<html lang="en">
<head>
<meta charset="utf-8">
<title>BRM Constructions – Business Cards</title>
<link href="https://fonts.googleapis.com/css2?family=Open+Sans:wght@400;600;700&display=swap" rel="stylesheet">
<style>
  :root {
    --backdrop: #2b2d31;
    --card-front: #4a4a4b;
    --card-back: #0e0e0f;
    --text-white: #ffffff;
    --text-charcoal: #6d6d6f;
    --text-light: #b9b9bb;
    --text-muted: #8c8c8e;
    --rule: #4a4a4c;
  }
  * { margin: 0; padding: 0; box-sizing: border-box; }
  html, body {
    width: 1200px;
    height: 864px;
    overflow: hidden;
    background: var(--backdrop);
    font-family: "Open Sans", Arial, sans-serif;
  }
  .canvas {
    position: relative;
    width: 1200px;
    height: 864px;
  }
  .card {
    position: absolute;
    width: 560px;
    height: 320px;
    border-radius: 4px;
    box-shadow: 0 14px 30px rgba(0, 0, 0, 0.45);
  }
  .card--front {
    left: 140px;
    top: 80px;
    background: var(--card-front);
    display: flex;
    align-items: center;
    justify-content: center;
  }
  .card--back {
    left: 500px;
    top: 460px;
    background: var(--card-back);
  }
  .brand-name {
    font-weight: 700;
    font-size: 46px;
    letter-spacing: 1px;
    color: var(--text-white);
    line-height: 1;
    white-space: nowrap;
  }
  .card--back .brand-name {
    position: absolute;
    right: 40px;
    top: 60px;
    font-size: 36px;
    color: var(--text-charcoal);
  }
  .holder {
    position: absolute;
    left: 40px;
    top: 112px;
  }
  .holder-name {
    font-weight: 600;
    font-size: 19px;
    color: var(--text-light);
  }
  .holder-role {
    font-size: 13px;
    color: var(--text-muted);
    margin-top: 2px;
  }
  .divider {
    position: absolute;
    left: 240px;
    right: 0;
    top: 150px;
    height: 1px;
    background: var(--rule);
  }
  .contact {
    position: absolute;
    right: 30px;
    top: 170px;
    text-align: right;
    list-style: none;
  }
  .contact li {
    font-size: 15px;
    color: var(--text-light);
    line-height: 24px;
    display: flex;
    align-items: center;
    justify-content: flex-end;
    gap: 8px;
  }
  .contact .abn {
    color: var(--text-muted);
    font-weight: 600;
    margin-bottom: 8px;
    padding-right: 22px;
  }
  .contact .abn strong { color: var(--text-light); font-weight: 700; }
  .contact svg { width: 14px; height: 14px; fill: var(--text-muted); flex: none; }
</style>
</head>
<body>
<main class="canvas">
  <section class="card card--front" aria-label="Business card front">
    <h1 class="brand-name">BRM CONSTRUCTIONS</h1>
  </section>

  <section class="card card--back" aria-label="Business card back">
    <p class="brand-name">BRM CONSTRUCTIONS</p>
    <div class="holder">
      <p class="holder-name">Daniel Harper</p>
      <p class="holder-role">Managing Director</p>
    </div>
    <div class="divider"></div>
    <ul class="contact">
      <li class="abn">ABN NO: <strong>12345</strong></li>
      <li>(044)-555-0182
        <svg viewBox="0 0 16 16" aria-hidden="true"><path d="M3.5 1.5l2.5 0 1 3.5-1.8 1.3a8 8 0 0 0 4.5 4.5l1.3-1.8 3.5 1v2.5c0 .8-.7 1.5-1.5 1.5C7 14 2 9 2 3c0-.8.7-1.5 1.5-1.5z"/></svg>
      </li>
      <li>info@brmbuild.com
        <svg viewBox="0 0 16 16" aria-hidden="true"><path d="M1 3h14v10H1zM2 4.2v.4l6 4 6-4v-.4z"/></svg>
      </li>
      <li>www.brmbuild.com
        <svg viewBox="0 0 16 16" aria-hidden="true"><circle cx="8" cy="8" r="7"/><path d="M1 8h14M8 1c-3 3.5-3 10.5 0 14M8 1c3 3.5 3 10.5 0 14" stroke="#0e0e0f" stroke-width="1.1" fill="none"/></svg>
      </li>
    </ul>
  </section>
</main>
</body>
</html>
```